Specialist aerospace company requires Powerpoint template

We are a company who delivers specialist engineering and testing services. We would like an updated Powerpoint template - specifically one that will be suitable to use in the production of training materials.
We would therefore like the following included:
-Our logo
-A copyright notice
-The course name (e.g. High Voltage Basics)
-The lesson name (e.g. Safe Clearances)
We wish to convey a professional image.

```html
<!DOCTYPE html>
<html lang="en">
<head>
<meta charset="utf-8">
<title>Altivolt Training Template</title>
<link href="https://fonts.googleapis.com/css2?family=Poppins:wght@400;500;600;700;800&display=swap" rel="stylesheet">
<style>
:root{
  --page:#aaa9aa;
  --navy:#1f3a5f;
  --blue:#42709b;
  --slate:#3f4b57;
  --ink:#38424d;
  --text:#5a6470;
  --white:#ffffff;
  --photo-a:#5b7c9c;
  --photo-b:#2c3e52;
}
*{margin:0;padding:0;box-sizing:border-box}
html,body{width:1200px;height:1072px;overflow:hidden;background:var(--page);font-family:'Poppins',sans-serif}
.canvas{position:relative;width:1200px;height:1072px}
.slide{position:absolute;width:545px;height:306px;background:var(--white);overflow:hidden}
.s1{left:38px;top:45px}.s2{left:618px;top:45px}
.s3{left:38px;top:380px}.s4{left:618px;top:380px}
.s5{left:38px;top:721px}.s6{left:618px;top:721px}
.edge{position:absolute;right:0;top:0;width:3px;height:100%;background:var(--blue)}
.abs{position:absolute}
.photo{position:absolute;border-radius:50%;background:linear-gradient(150deg,var(--photo-a),var(--photo-b))}
.brand{position:absolute;left:9px;top:276px;display:flex;align-items:center;gap:5px;font-weight:500;font-size:19px;color:var(--slate);letter-spacing:-.3px}
.brand i{width:16px;height:16px;background:var(--blue);display:block}
.copy{position:absolute;top:287px;font-size:5px;color:var(--ink)}
.s2 .copy,.s4 .copy,.s6 .copy{left:410px}
.s3 .copy,.s5 .copy{left:410px}
.tab{position:absolute;right:3px;bottom:0;width:28px;height:26px}
.tab span{position:absolute;left:8px;top:10px;font-size:8px;font-weight:700;color:var(--white)}
.title{position:absolute;font-weight:800;font-size:19px;color:var(--ink);letter-spacing:.3px;line-height:1}
.body{position:absolute;font-size:5.6px;line-height:8.5px;color:var(--text);text-align:justify}
.body p+p{margin-top:8.5px}
/* cover */
.cover-bg{position:absolute;inset:0;background:linear-gradient(120deg,#1b3558 0%,#2d4d78 45%,#23406a 100%)}
.cover-brand{position:absolute;left:124px;top:86px;display:flex;align-items:center;gap:8px;color:var(--white);font-weight:500;font-size:34px;letter-spacing:-.5px}
.cover-brand i{width:30px;height:30px;background:var(--white);display:block}
.tagline{position:absolute;left:0;width:545px;top:156px;text-align:center;color:var(--white);font-weight:700;font-size:16.5px;line-height:20px}
.course{position:absolute;top:207px;color:var(--white);font-size:8.6px}
.course b{font-weight:700}
.cover-copy{position:absolute;top:285px;left:0;width:545px;text-align:center;font-size:5px;color:var(--white)}
/* services */
.centered{text-align:center}
.svc{position:absolute;top:86px;width:110px;text-align:center}
.svc .photo{position:relative;width:93px;height:93px;margin:0 auto}
.svc h3{margin-top:4px;font-size:10px;font-weight:600;color:var(--ink)}
.svc p{margin-top:3px;font-size:5.7px;line-height:11.3px;color:var(--text)}
/* why */
.feat{position:absolute;top:201px;width:70px;text-align:center}
.feat .dot{width:44px;height:44px;margin:0 auto;border-radius:50%;background:var(--white);box-shadow:0 1px 5px rgba(0,0,0,.15);display:flex;align-items:center;justify-content:center}
.feat p{margin-top:6px;font-size:7px;font-weight:500;color:var(--ink)}
/* contact */
.contact{position:absolute;top:100px;width:128px;height:128px;border-radius:50%;color:var(--white);text-align:center}
.contact .ic{width:34px;height:34px;border-radius:50%;background:var(--white);margin:32px auto 0;display:flex;align-items:center;justify-content:center}
.contact h4{margin-top:8px;font-size:7px;font-weight:600}
.contact p{margin-top:3px;font-size:4.8px;line-height:8.4px}
</style>
</head>
<body>
<div class="canvas">

<!-- 01 cover -->
<section class="slide s1">
  <div class="cover-bg" role="img" aria-label="Engineer in hard hat overlaid on city skyline at dusk, blue tint"></div>
  <svg class="abs" style="left:0;top:0" width="545" height="306">
    <circle cx="500" cy="10" r="80" fill="#ffffff" opacity=".55"/>
    <circle cx="532" cy="-5" r="78" fill="#ffffff"/>
    <circle cx="40" cy="268" r="100" fill="#8ea5c6" opacity=".45"/>
  </svg>
  <div class="cover-brand"><i></i>Altivolt</div>
  <h1 class="tagline">We are a company who delivers specialist<br>engineering and testing services.</h1>
  <p class="course" style="left:93px">The course name : <b>High Voltage Basics</b></p>
  <p class="course" style="left:283px">The lesson name : <b>Safe Clearances</b></p>
  <p class="cover-copy">© Copyrights 2023 | All Rights Reserved</p>
</section>

<!-- 02 about -->
<section class="slide s2">
  <svg class="abs" style="left:0;top:0" width="545" height="306">
    <path d="M320 0 H542 V185 C500 240 420 250 360 200 C300 140 300 50 320 0Z" fill="var(--blue)"/>
  </svg>
  <div class="photo" style="left:276px;top:10px;width:256px;height:256px" role="img" aria-label="Engineer in hard hat and safety glasses holding a laptop"></div>
  <h2 class="title" style="left:21px;top:35px">ABOUT US</h2>
  <div class="body" style="left:21px;top:64px;width:233px">
    <p>Lorem ipsum dolor sit amet, consectetur adipiscing elit, sed do eiusmod tempor incididunt ut labore et dolore magna aliqua. Ut enim ad minim veniam, quis nostrud exercitation ullamco laboris nisi ut aliquip ex ea commodo consequat. Duis aute irure dolor in reprehenderit in voluptate velit esse cillum dolore eu fugiat nulla pariatur. Excepteur sint occaecat cupidatat non proident, sunt in culpa qui officia deserunt mollit anim id est laborum.</p>
    <p>Lorem ipsum dolor sit amet, consectetur adipiscing elit, sed do eiusmod tempor incididunt ut labore et dolore magna aliqua. Ut enim ad minim veniam, quis nostrud exercitation ullamco laboris nisi ut aliquip ex ea commodo consequat. Duis aute irure dolor in reprehenderit in voluptate velit esse cillum dolore eu fugiat nulla pariatur. Excepteur sint occaecat cupidatat non proident, sunt in culpa qui officia deserunt mollit anim id est laborum.</p>
    <p>Lorem ipsum dolor sit amet, consectetur adipiscing elit, sed do eiusmod tempor incididunt ut labore et dolore magna aliqua. Ut enim ad minim veniam, quis nostrud exercitation ullamco laboris nisi ut aliquip ex ea commodo consequat. Duis aute irure dolor in reprehenderit in voluptate velit esse cillum dolore eu fugiat nulla pariatur. Excepteur sint occaecat cupidatat non proident, sunt in culpa qui officia deserunt mollit anim id est laborum.</p>
  </div>
  <div class="brand"><i></i>Altivolt</div>
  <p class="copy">© Copyrights 2023 | All Rights Reserved</p>
  <svg class="tab" viewBox="0 0 28 26"><polygon points="3,0 28,0 28,26 0,26" fill="var(--blue)"/></svg>
  <div class="tab"><span>02</span></div>
  <div class="edge"></div>
</section>

<!-- 03 services -->
<section class="slide s3">
  <h2 class="title centered" style="left:0;width:545px;top:21px">OUR SERVICES</h2>
  <p class="body centered" style="left:64px;top:50px;width:417px;text-align:center">Lorem ipsum dolor sit amet, consectetur adipiscing elit, sed do eiusmod tempor incididunt ut labore et dolore magna aliqua. Ut enim ad minim veniam, quis nostrud exercitation ullamco laboris nisi ut aliquip ex ea commodo consequat. Duis aute irure dolor in reprehenderit in voluptate velit esse cillum dolore eu fugiat nulla pariatur.</p>
  <div class="svc" style="left:32px"><div class="photo" role="img" aria-label="Smiling engineer working at a laptop"></div><h3>Nemo enim ipsam</h3><p>Lorem ipsum dolor sit amet, consectetur adipiscing elit, sed do eiusmod tempor incididunt ut labore et dolore magna aliqua.</p></div>
  <div class="svc" style="left:155px"><div class="photo" role="img" aria-label="Technician operating a lathe machine"></div><h3>Nemo enim ipsam</h3><p>Lorem ipsum dolor sit amet, consectetur adipiscing elit, sed do eiusmod tempor incididunt ut labore et dolore magna aliqua.</p></div>
  <div class="svc" style="left:278px"><div class="photo" role="img" aria-label="Team discussing around a screen"></div><h3>Nemo enim ipsam</h3><p>Lorem ipsum dolor sit amet, consectetur adipiscing elit, sed do eiusmod tempor incididunt ut labore et dolore magna aliqua.</p></div>
  <div class="svc" style="left:402px"><div class="photo" role="img" aria-label="Site engineer in safety vest reading plans"></div><h3>Nemo enim ipsam</h3><p>Lorem ipsum dolor sit amet, consectetur adipiscing elit, sed do eiusmod tempor incididunt ut labore et dolore magna aliqua.</p></div>
  <div class="brand"><i></i>Altivolt</div>
  <p class="copy">© Copyrights 2023 | All Rights Reserved</p>
  <svg class="tab" viewBox="0 0 28 26"><polygon points="3,0 28,0 28,26 0,26" fill="var(--blue)"/></svg>
  <div class="tab"><span>03</span></div>
  <div class="edge"></div>
</section>

<!-- 04 why -->
<section class="slide s4">
  <svg class="abs" style="left:0;top:0" width="545" height="306">
    <defs><linearGradient id="wg" x1="0" y1="0" x2="1" y2="0"><stop offset="0" stop-color="var(--blue)"/><stop offset="1" stop-color="var(--slate)"/></linearGradient></defs>
    <path d="M0 0 H154 C180 40 190 120 150 160 C110 190 40 160 0 140Z" fill="url(#wg)"/>
  </svg>
  <div class="photo" style="left:33px;top:22px;width:164px;height:164px" role="img" aria-label="Two engineers in hard hats reviewing a tablet in a plant"></div>
  <div class="photo" style="left:384px;top:162px;width:176px;height:176px;background:var(--blue);opacity:.9" role="img" aria-label="Faded blue-toned photo of engineers on site"></div>
  <div class="abs" style="left:380px;top:272px;width:165px;height:34px;background:var(--white)"></div>
  <h2 class="title" style="right:30px;top:21px">WHY CHOOSE US</h2>
  <div class="body" style="left:269px;top:50px;width:246px;text-align:right">
    <p>Lorem ipsum dolor sit amet, consectetur adipiscing elit, sed do eiusmod tempor incididunt ut labore et dolore magna aliqua. Ut enim ad minim veniam, quis nostrud exercitation ullamco laboris nisi ut aliquip ex ea commodo consequat.</p>
    <p>Duis aute irure dolor in reprehenderit in voluptate velit esse cillum dolore eu fugiat nulla pariatur. Excepteur sint occaecat cupidatat non proident, sunt in culpa qui officia deserunt mollit anim id est laborum. Lorem ipsum dolor sit amet, consectetur adipiscing elit, sed do eiusmod tempor incididunt ut labore et dolore magna aliqua. Ut enim ad minim veniam, quis nostrud exercitation ullamco laboris nisi ut aliquip ex ea commodo consequat. Duis aute irure dolor in reprehenderit in voluptate velit esse cillum dolore eu fugiat nulla pariatur. Excepteur sint occaecat cupidatat non proident, sunt in culpa qui officia deserunt mollit anim id est laborum.</p>
  </div>
  <div class="feat" style="left:14px"><div class="dot"><svg width="20" height="20" viewBox="0 0 20 20" fill="none" stroke="var(--slate)" stroke-width="1.1"><circle cx="10" cy="6" r="3.5"/><path d="M6 5.5 Q10 1 14 5.5"/><path d="M3 19 V15 Q10 9 17 15 V19"/></svg></div><p>Duis aute irure</p></div>
  <div class="feat" style="left:109px"><div class="dot"><svg width="20" height="20" viewBox="0 0 20 20" fill="none" stroke="var(--slate)" stroke-width="1.1"><circle cx="6" cy="6" r="3"/><circle cx="14" cy="10" r="3"/><circle cx="6" cy="15" r="2.5"/></svg></div><p>Duis aute irure</p></div>
  <div class="feat" style="left:204px"><div class="dot"><svg width="20" height="20" viewBox="0 0 20 20" fill="none" stroke="var(--slate)" stroke-width="1.2"><path d="M3 17 L17 3"/><path d="M3 3 L17 17"/><circle cx="4" cy="4" r="2"/><circle cx="16" cy="16" r="2"/></svg></div><p>Duis aute irure</p></div>
  <div class="feat" style="left:298px"><div class="dot"><svg width="20" height="20" viewBox="0 0 20 20" fill="none" stroke="var(--slate)" stroke-width="1.1"><rect x="3" y="4" width="14" height="9"/><path d="M10 13 V17 M6 17 H14"/><circle cx="10" cy="8.5" r="2"/></svg></div><p>Duis aute irure</p></div>
  <div class="brand"><i></i>Altivolt</div>
  <p class="copy">© Copyrights 2023 | All Rights Reserved</p>
  <svg class="tab" viewBox="0 0 28 26"><polygon points="3,0 28,0 28,26 0,26" fill="var(--blue)"/></svg>
  <div class="tab"><span>04</span></div>
  <div class="edge"></div>
</section>

<!-- 05 solution -->
<section class="slide s5">
  <svg class="abs" style="left:0;top:0" width="545" height="306">
    <defs><linearGradient id="sg" x1="0" y1="0" x2="1" y2="0"><stop offset="0" stop-color="var(--blue)"/><stop offset="1" stop-color="var(--slate)"/></linearGradient></defs>
    <circle cx="467" cy="0" r="49" fill="url(#sg)"/>
    <circle cx="124" cy="198" r="127" fill="var(--blue)"/>
  </svg>
  <div class="photo" style="left:-15px;top:36px;width:253px;height:253px" role="img" aria-label="Two engineers in hard hats pointing across a factory floor"></div>
  <div class="abs" style="left:0;top:272px;width:300px;height:34px;background:var(--white)"></div>
  <h2 class="title" style="right:28px;top:86px">OUR SOLUTION</h2>
  <div class="body" style="left:270px;top:115px;width:246px;text-align:right">
    <p>Lorem ipsum dolor sit amet, consectetur adipiscing elit, sed do eiusmod tempor incididunt ut labore et dolore magna aliqua. Ut enim ad minim veniam, quis nostrud exercitation ullamco laboris nisi ut aliquip ex ea commodo consequat.</p>
    <p>Duis aute irure dolor in reprehenderit in voluptate velit esse cillum dolore eu fugiat nulla pariatur. Excepteur sint occaecat cupidatat non proident, sunt in culpa qui officia deserunt mollit anim id est laborum. Lorem ipsum dolor sit amet, consectetur adipiscing elit, sed do eiusmod tempor incididunt ut labore et dolore magna aliqua. Ut enim ad minim veniam, quis nostrud exercitation ullamco laboris nisi ut aliquip ex ea commodo consequat. Duis aute irure dolor in reprehenderit in voluptate velit esse cillum dolore eu fugiat nulla pariatur. Excepteur sint occaecat cupidatat non proident, sunt in culpa qui officia deserunt mollit anim id est laborum.</p>
  </div>
  <div class="brand"><i></i>Altivolt</div>
  <p class="copy">© Copyrights 2023 | All Rights Reserved</p>
  <svg class="tab" viewBox="0 0 28 26"><polygon points="3,0 28,0 28,26 0,26" fill="var(--blue)"/></svg>
  <div class="tab"><span>05</span></div>
  <div class="edge"></div>
</section>

<!-- 06 thank you -->
<section class="slide s6">
  <h2 class="title centered" style="left:0;width:545px;top:26px">THANK YOU</h2>
  <p class="body" style="left:90px;top:56px;width:365px;text-align:center">Lorem ipsum dolor sit amet, consectetur adipiscing elit, sed do eiusmod tempor incididunt ut labore et dolore magna aliqua. Ut enim ad minim veniam, quis nostrud exercitation ullamco laboris nisi ut aliquip ex ea commodo consequat. Duis aute irure dolor in reprehenderit in voluptate velit esse cillum dolore eu fugiat nulla pariatur.</p>
  <div class="contact" style="left:68px;background:var(--blue)">
    <div class="ic"><svg width="10" height="12" viewBox="0 0 10 12"><path d="M5 0 C2 0 0 2 0 4.6 C0 8 5 12 5 12 C5 12 10 8 10 4.6 C10 2 8 0 5 0Z" fill="var(--blue)"/><circle cx="5" cy="4.6" r="1.7" fill="#fff"/></svg></div>
    <h4>Address :</h4><p>123,Lorem ipsum dolor sit amet,<br>consectetur adipiscing</p>
  </div>
  <div class="contact" style="left:209px;background:var(--slate)">
    <div class="ic"><svg width="10" height="10" viewBox="0 0 24 24"><path d="M6.6 10.8a15 15 0 0 0 6.6 6.6l2.2-2.2c.3-.3.7-.4 1-.2 1.1.4 2.3.6 3.6.6.6 0 1 .4 1 1V20c0 .6-.4 1-1 1A17 17 0 0 1 3 4c0-.6.4-1 1-1h3.5c.6 0 1 .4 1 1 0 1.3.2 2.5.6 3.6.1.3 0 .7-.2 1z" fill="var(--slate)"/></svg></div>
    <h4>Phone :</h4><p>+1 888 888 8888</p>
  </div>
  <div class="contact" style="left:351px;background:var(--blue)">
    <div class="ic"><svg width="11" height="9" viewBox="0 0 11 9"><rect width="11" height="9" rx="1" fill="var(--blue)"/><path d="M0.5 1 L5.5 5 L10.5 1" stroke="#fff" stroke-width="1" fill="none"/></svg></div>
    <h4>Email Address :</h4><p>info@companyname.com</p>
  </div>
  <div class="brand"><i></i>Altivolt</div>
  <p class="copy">© Copyrights 2023 | All Rights Reserved</p>
  <svg class="tab" viewBox="0 0 28 26"><polygon points="3,0 28,0 28,26 0,26" fill="var(--blue)"/></svg>
  <div class="tab"><span>06</span></div>
  <div class="edge"></div>
</section>

</div>
</body>
</html>
```